Wordpress Theme for Medical Clinics

** Please view updated Sitemap2.pdf doc to clarify some confusion ***

This is a multiuser WordPress subscription site for medical clinics. Please see attachment for sitemap. Please do not include extra content like social media icons, search bars, or images. If you have questions, please ask for clarification.
The site contains the following pages and sub-pages:

1. Home
2. Our Clinic
2a. Our Clinic > Mission
2b. Our Clinic > Services
2c. Our Clinic > Clinic Policies
2d. Our Clinic > Schedules
3. Our Staff
3a. Our Staff > [Staff member page]
4. Resources
4a. Resources > Patient Health (index)
4b. Resources > Patient Health (index) > [post]
4c. Resources > Links
4d. Resources > Forms
5. Alerts
5a. Alerts > [Alert Page]
6. Contact Us

Includes the Following Pages, Subpages, and Content
1. Home
a. About Us
b. Our Staff
c. Bulletins
d. Accepting New Patients (shown as an alert widget)
e. Links
i. Physician Toolbox
ii. Book an Appointment
f. Clinic Policies
i. Show first 3 policies (e.g. Late Arrivals, Missed Appointments, Fees)
ii. Link to Clinic Policies page
g. Primary widget (displayed on all pages)
i. Hours of operation
ii. Contact Info
1. Tel
2. Fax
3. Email
4. Address
5. Get directions (link to Google Maps)
2. Our Clinic
a. Main Page
i. Clinic Name
ii. Overview
iii. Languages Spoken
iv. Secondary Navigation
1. Mission
2. Services
3. Clinic Policies
4. Schedules (see attachment)
b. Our Clinic > Mission
c. Our Clinic > Services
i. For each service include service TITLE and DESCRIPTION
d. Our Clinic > Clinic Policies
i. For each policy include policy TITLE and DESCRIPTION
ii. Include the following policies in mockup
1. Late arrivals
2. Missed appointments
3. Fees for missed appointments
4. Referrals and follow-ups
5. Services not covered by RDA
6. Information for LTF patients
7. Medical Legal Reports
e. Our Clinic > Schedules
3. Our Staff
a. Main Page
i. Display a list of staff members. Include NAME and DESIGNATION
b. Our Staff > [Staff Name]
i. Include NAME, PICTURE, DESIGNATION, and BIO
4. Resources
a. Resources > Patient Health
i. Main Page
1. Posts (ordered by date)
a. Title
b. Summary
2. Side Navigation
a. Post Categories
ii. Patient Health > [post title]
1. Title
2. Post Category
3. Date
4. Author
5. Summary
6. Body
b. Resources > Links
1. Secondary Navigation - Categories
a. Sample Categories:
i. Local Services
ii. RDA and Drug Coverage
iii. Mental Health Resources
2. Category page
a. Include the following links in the 'Local Services' category
i. Hypertension clinics
ii. Home Care services
iii. Vaccine Clinics
c. Resources > Forms
i. Display a table with form TITLE and CATEGORY
ii. Side Navigation
1. Form Categories
a. Use the following sample Categories
i. Referrals
ii. Insurance
iii. Intake
iv. Discharge
v. Waivers
5. Alerts
a. Main page
i. List of all Alert posts
1. Include post TITLE as a link to the post
ii. Side Navigation
1. Alerts Archive
a. shown as Month + Number of posts
iii. Alerts > [Alert page]
1. Include TITLE, DATE, AUTHOR, BODY
6. Contact Us
a. Map
b. Hours of operation
c. Address
d. Phone number
e. Fax number
e. Fax number
f. Map
g. Email

Design notes:
- fixed width
- responsive (need designs for mobile, tablet, and desktop)
- simple, dark font, white background
- use Font Awesome icons where needed
- user adds own logo

Target Market(s)

Medical Clinics

Industry/Entity Type

Medical

Number of Pages Required

5+ page

Font styles to use
Serif
Sans Serif

Requirements
Must have
• Please keep designs very simple.
• Examples:
• https://www.quolbin.com/install
• http://www.ventrohax.com/company/about-us
• http://brindlequota.org/
• http://www.trosk.com/
Should not have
• Minimal or no use of shadows and gradients

```html
<!DOCTYPE html>
<html lang="en">
<head>
<meta charset="utf-8">
<title>Medical – Alerts</title>
<link href="https://fonts.googleapis.com/css2?family=Open+Sans:wght@300;400;600;700&display=swap" rel="stylesheet">
<style>
:root{
  --blue:#1479c9;
  --ink:#333538;
  --muted:#8796a3;
  --body:#6b7580;
  --rule:#e6e9ec;
  --side:#f3f4f5;
  --footer:#363638;
  --footer-deep:#2e2e30;
  --footer-text:#d5d6d8;
}
*{margin:0;padding:0;box-sizing:border-box}
html,body{width:1000px;height:1200px;overflow:hidden}
body{background:var(--side);font-family:"Open Sans",Arial,sans-serif;color:var(--ink);position:relative}
.page{position:absolute;left:23px;top:0;width:950px;height:1200px;background:#fff}
.abs{position:absolute}
a{color:inherit;text-decoration:none}

.topbar{position:absolute;left:0;top:0;width:1000px;height:24px;border-top:1px solid #bfe0f5;border-bottom:1px solid #eef0f2;font-size:8.5px;color:#8a9097}
.topbar .contact{left:91px;top:7px}
.topbar .contact b{font-weight:600;color:#7b8188}
.topbar .links{right:97px;top:5px;display:flex;align-items:center;gap:9px}
.topbar .links span{display:flex;align-items:center;gap:5px}

.brand{display:flex;align-items:center;gap:8px;font-size:21px;font-weight:400;color:var(--ink)}
.brand i{display:block;width:36px;height:36px;border-radius:50%;background:var(--blue)}
.header .brand{left:91px;top:38px}
.nav{left:549px;top:47px;font-size:12px;color:var(--ink)}
.nav a{position:absolute;white-space:nowrap}
.nav .active{color:var(--blue)}
.nav-marker{left:810px;top:84px;width:32px;height:3px;background:var(--blue)}
.header-shade{left:112px;top:88px;width:770px;height:6px;background:linear-gradient(#eceeef,rgba(255,255,255,0));border-radius:0 0 50% 50%}

.title{left:91px;top:108px;font-size:19px;font-weight:300;color:var(--blue)}
.crumbs{left:157px;top:117px;font-size:8.5px;color:#7b8188}
.crumbs u{text-decoration:underline}
.title-rule{left:91px;top:143px;width:814px;height:1px;background:var(--rule)}
.title-mark{left:91px;top:142px;width:62px;height:2px;background:var(--blue)}

.alert{left:89px;width:540px;height:170px}
.date{position:absolute;left:0;top:0;width:95px;height:95px;background:var(--blue);color:#fff;text-align:center;font-weight:300}
.date .m{display:block;font-size:23px;margin-top:16px}
.date .d{display:block;font-size:21px;margin-top:6px}
.date sup{font-size:12px}
.alert h2{position:absolute;left:144px;top:0;font-size:17px;font-weight:600;color:var(--ink);white-space:nowrap}
.alert .sub{position:absolute;left:142px;top:26px;font-size:14px;color:var(--muted);font-weight:400}
.alert .rule{position:absolute;left:142px;top:54px;width:280px;height:2px;background:var(--rule)}
.alert .rule::before{content:"";position:absolute;left:0;top:0;width:62px;height:2px;background:var(--blue)}
.alert p{position:absolute;left:147px;top:80px;width:400px;font-size:9.3px;line-height:14.3px;color:var(--body);white-space:nowrap}
.alert .more{position:absolute;left:143px;font-size:9px;color:var(--blue)}
.alert .more u{text-decoration:underline}

.pager{left:89px;top:777px;display:flex;gap:3px}
.pager span{width:22px;height:22px;border:1px solid var(--blue);color:var(--blue);font-size:9px;display:flex;align-items:center;justify-content:center}
.pager .on{background:var(--blue);color:#fff}

.archives{left:702px;top:168px;width:203px}
.archives h3{font-size:12.5px;font-weight:400;color:#555a60;margin-bottom:13px}
.archives ul{margin-top:-6px}
.archives li{list-style:none;height:28px;border-bottom:1px solid var(--rule);display:flex;align-items:center;gap:7px;font-size:9px;color:#7b8188}
.archives li.on{color:var(--blue)}

.footer{left:23px;top:843px;width:950px;height:306px;background:var(--footer);color:var(--footer-text);font-size:9px}
.legal{left:23px;top:1149px;width:950px;height:51px;background:var(--footer-deep);color:var(--footer-text);font-size:8.5px}
.legal p{position:absolute;left:67px;top:20px}
.footer h4{position:absolute;top:51px;font-size:10px;font-weight:700;color:#fff;text-transform:uppercase}
.footer .brand{position:absolute;left:67px;top:41px;color:#fff}
.footer .lead{position:absolute;left:67px;top:90px;width:160px;line-height:15px}
.footer .row{position:absolute;left:67px;display:flex;gap:10px;line-height:15.5px}
.footer .row svg{flex:none;margin-top:2px}
.footer .menu{position:absolute;left:269px;top:90px;list-style:none;font-size:9.8px}
.footer .menu li{height:21.3px;display:flex;gap:9px;color:#e4e5e7}
.footer .posts{position:absolute;left:474px;width:185px;line-height:15.5px}
.footer .posts .t{display:flex;gap:6px}
.footer .posts b{color:#fff;font-weight:600}
.footer .posts small{display:block;font-size:8px;color:#4aa3e6;margin-left:12px;margin-top:2px}
.footer .news{position:absolute;left:679px;top:90px;width:160px;line-height:15px}
.footer .sub-form{position:absolute;left:679px;top:126px;display:flex;width:186px;height:21px}
.footer .sub-form .field{flex:1;background:#e9eaeb;color:#9a9fa4;font-size:8.5px;padding:4px 7px}
.footer .sub-form .btn{width:61px;background:var(--blue);color:#fff;font-size:9px;text-align:center;line-height:21px}
</style>
</head>
<body>
<div class="page"></div>

<div class="topbar">
  <div class="abs contact"><b>Call Us Today!</b> &nbsp;+123 482 917 &nbsp;&nbsp;|&nbsp;&nbsp; contact@mendora-clinic.org</div>
  <div class="abs links">
    <span><svg width="10" height="12" viewBox="0 0 10 12"><rect x="0.5" y="1.5" width="9" height="10" fill="none" stroke="#9aa0a6"/><rect x="3" y="0" width="4" height="3" fill="#9aa0a6"/></svg>Book an Appointment</span>
    <span>|</span>
    <span><svg width="13" height="11" viewBox="0 0 13 11"><rect x="0.5" y="2.5" width="12" height="8" fill="none" stroke="#9aa0a6"/><rect x="4.5" y="0.5" width="4" height="2" fill="none" stroke="#9aa0a6"/><path d="M6.5 4.5v4M4.5 6.5h4" stroke="#9aa0a6"/></svg>Physician Toolbox</span>
  </div>
</div>

<header class="header">
  <div class="abs brand"><i></i>Medical</div>
  <nav class="abs nav">
    <a style="left:0">Home</a>
    <a style="left:58px">Our Clinic</a>
    <a style="left:134px">Staff</a>
    <a style="left:182px">Resources</a>
    <a class="active" style="left:261px">Alerts</a>
    <a style="left:315px">Contact</a>
  </nav>
  <div class="abs nav-marker"></div>
  <div class="abs header-shade"></div>
</header>

<div class="abs title">Alerts</div>
<div class="abs crumbs"><u>Home</u> &nbsp;›&nbsp; Alerts</div>
<div class="abs title-rule"></div>
<div class="abs title-mark"></div>

<article class="abs alert" style="top:173px">
  <div class="date"><span class="m">May</span><span class="d">23<sup>th</sup></span></div>
  <h2>Harriet Vale, Prof</h2>
  <div class="sub">Pediatric Clinic</div>
  <div class="rule"></div>
  <p style="left:151px;top:68px">Integer iaculis egestas odio, vel dictum turpis placerat id ellentesque semper nisl eget<br>aliquam vel vehicula dui nam sit amet ultricies sapien.<br>Nulla euismod vitae justo a ullamcorper. In rhoncus nisi massa, sit amet tristique augue<br>Proin aliquet rhoncus magna vel scelerisque. Nulla facilisi. Aliquam ut scelerisque nulla.</p>
  <a class="more" style="top:139px"><u>View More</u> &nbsp;»</a>
</article>

<article class="abs alert" style="top:376px">
  <div class="date"><span class="m">May</span><span class="d">21<sup>th</sup></span></div>
  <h2>Corinne Ashby, Prof</h2>
  <div class="sub">Pediatric Clinic</div>
  <div class="rule"></div>
  <p style="top:73px">Integer iaculis egestas odio, vel dictum turpis placerat id ellentesque semper nisl eget<br>aliquam vel vehicula dui nam sit amet ultricies sapien.<br>Nulla euismod vitae justo a ullamcorper. In rhoncus nisi massa, sit amet tristique augue<br>Proin aliquet rhoncus magna vel scelerisque. Nulla facilisi. Aliquam ut scelerisque nulla.</p>
  <a class="more" style="top:138px"><u>View More</u> &nbsp;»</a>
</article>

<article class="abs alert" style="top:582px">
  <div class="date"><span class="m">May</span><span class="d">19<sup>th</sup></span></div>
  <h2>Harriet Vale, Prof</h2>
  <div class="sub">Pediatric Clinic</div>
  <div class="rule"></div>
  <p style="top:74px">Integer iaculis egestas odio, vel dictum turpis placerat id ellentesque semper nisl eget<br>aliquam vel vehicula dui nam sit amet ultricies sapien.<br>Nulla euismod vitae justo a ullamcorper. In rhoncus nisi massa, sit amet tristique augue<br>Proin aliquet rhoncus magna vel scelerisque. Nulla facilisi. Aliquam ut scelerisque nulla.</p>
  <a class="more" style="top:138px"><u>View More</u> &nbsp;»</a>
</article>

<nav class="abs pager">
  <span><svg width="6" height="9" viewBox="0 0 6 9"><path d="M5 1L1.5 4.5 5 8" fill="none" stroke="#1479c9" stroke-width="1.5"/></svg></span>
  <span class="on">1</span><span>2</span><span>3</span>
  <span><svg width="6" height="9" viewBox="0 0 6 9"><path d="M1 1l3.5 3.5L1 8" fill="none" stroke="#1479c9" stroke-width="1.5"/></svg></span>
</nav>

<aside class="abs archives">
  <h3>Archives</h3>
  <ul>
    <li><svg width="13" height="13" viewBox="0 0 13 13"><circle cx="6.5" cy="6.5" r="6" fill="none" stroke="#9aa0a6"/><path d="M5.5 4l2.5 2.5-2.5 2.5" fill="none" stroke="#9aa0a6"/></svg>June 2015 &nbsp;(3)</li>
    <li class="on"><svg width="13" height="13" viewBox="0 0 13 13"><circle cx="6.5" cy="6.5" r="6.5" fill="#1479c9"/><path d="M5.5 4l2.5 2.5-2.5 2.5" fill="none" stroke="#fff" stroke-width="1.3"/></svg>May 2015 &nbsp;(7)</li>
    <li><svg width="13" height="13" viewBox="0 0 13 13"><circle cx="6.5" cy="6.5" r="6" fill="none" stroke="#9aa0a6"/><path d="M5.5 4l2.5 2.5-2.5 2.5" fill="none" stroke="#9aa0a6"/></svg>April 2015 &nbsp;(4)</li>
    <li><svg width="13" height="13" viewBox="0 0 13 13"><circle cx="6.5" cy="6.5" r="6" fill="none" stroke="#9aa0a6"/><path d="M5.5 4l2.5 2.5-2.5 2.5" fill="none" stroke="#9aa0a6"/></svg>March &nbsp;2015 &nbsp;(5)</li>
    <li><svg width="13" height="13" viewBox="0 0 13 13"><circle cx="6.5" cy="6.5" r="6" fill="none" stroke="#9aa0a6"/><path d="M5.5 4l2.5 2.5-2.5 2.5" fill="none" stroke="#9aa0a6"/></svg>February 2015 &nbsp;(2)</li>
  </ul>
</aside>

<footer class="abs footer">
  <div class="brand"><i></i>Medical</div>
  <p class="lead">Lorem ipsum dolor sit amet, teft consecte tur adipiscing.</p>
  <div class="row" style="top:139px"><svg width="9" height="12" viewBox="0 0 9 12"><path d="M4.5 0A4.5 4.5 0 0 0 0 4.5C0 8 4.5 12 4.5 12S9 8 9 4.5A4.5 4.5 0 0 0 4.5 0z" fill="#d5d6d8"/><circle cx="4.5" cy="4.5" r="1.7" fill="#363638"/></svg><span style="margin-left:4px">Medical &nbsp;Clinic<br>123 Elmridge Avenue<br>Larkton, NY 10160</span></div>
  <div class="row" style="top:200px"><svg width="10" height="10" viewBox="0 0 10 10"><path d="M2 0l2 2.5-1.2 1.3a6 6 0 0 0 3.4 3.4L7.5 6 10 8 8.5 10C4 10 0 6 0 1.5z" fill="#d5d6d8"/></svg><span>+123 482 917</span></div>
  <div class="row" style="top:215px"><svg width="10" height="10" viewBox="0 0 10 10"><rect x="2" y="0" width="6" height="3" fill="#d5d6d8"/><rect x="0" y="3.5" width="10" height="4" fill="#d5d6d8"/><rect x="2" y="7" width="6" height="3" fill="#d5d6d8"/></svg><span>+123 482 918</span></div>
  <div class="row" style="top:246px"><svg width="10" height="8" viewBox="0 0 10 8"><rect width="10" height="8" fill="#d5d6d8"/><path d="M0 0l5 4 5-4" fill="none" stroke="#363638"/></svg><span style="color:#fff;font-weight:600">contact@ mendora-clinic.org</span></div>

  <h4 style="left:269px">Our Clinic</h4>
  <ul class="menu">
    <li>›<span>Mission</span></li>
    <li>›<span>Services</span></li>
    <li>›<span>Schedules</span></li>
    <li>›<span>Policies</span></li>
    <li>›<span>More</span></li>
  </ul>

  <h4 style="left:474px">Resources</h4>
  <div class="posts" style="top:90px"><div class="t">›<span>Integer iaculis egestas odio, vel dictum turpis placerat id. Pellentesque semper nisl eget: <b>qk.to/RTSoouoUdg</b></span></div><small>2 days ago</small></div>
  <div class="posts" style="top:174px"><div class="t">›<span>Curabitur consequat tortor ut eros posu ere rutrum donec metus nisl, dictum vita fermentum: <b>qk.to/RTSoouoUdg</b></span></div><small>6 days ago</small></div>

  <h4 style="left:679px">Newsletter</h4>
  <p class="news">Ipsum dolor sit amet, teft consecte tur adipiscing elit ut eunt.</p>
  <div class="sub-form"><div class="field">Email Address</div><div class="btn">Subscribe</div></div>
</footer>

<div class="abs legal"><p>Copyright 2015 &nbsp;Medical | All Rights Reserved</p></div>
</body>
</html>
```